July 2022 Industrial Manufacturer Product Expo Mexico City

We manufacture large screws and fastners for large Mining equipment, Trains, large ships, airplanes, wind turbines, and so on. We also do custom work base on the customer needs. No matter the size we can make it.
We have a Expo coming up with companies all over the world. We have to stand out we are a family own business so our customer service will be above and beyond anyone can provide. We do not have a sales force to push our products and services we provide one on one service.
Plus@!! I'm looking for anything that you designers can come up with if it was your company to put on a business card, plus i want to do a 1 or 2 sided pamphlet, and then a website. We make Speciality Bolts for large mining equipment these bolts can be 3 to 4 foot long!!! Plus fasteners, Nuts, washers, any, size, strengths, special materials, we offer more of a ono on one customer service, We are a small company, family own, but can fulfill any type of orders. We can also provide special time lines for emergency orders. "We keep the machines running we here at KRV don't believe in down time" We want to hear any slogan based on our company to stand out.
Thanks i really appreciate all your work and options that we have to pick on. Plus just a thought we could possibly want to entertain a experience Marketing internet help maybe a employment possibility. Thanks

I need 2 cards one in Spanish and English Like the steel back ground maybe send me in some bright red and blue writing Same with the Black cards Please remove the word Military The logo KRV maybe integrate a picture of a Bolt 🔩 Thank you

Still looking for I need 2 cards one in Spanish and English Like the steel back ground maybe send me in some bright red and blue writing Same with the Black cards try bright writing Please remove the word Military The logo KRV maybe integrate a picture of a Bolt 🔩 Plus will need the company to make a brochure and website next Thank you

Target Market(s)

Large Mining, Ship, Train, Green Energy, VELM, and Government equipment. Throughout the World

Industry/Entity Type

We can Custom Manufacture any type of Fastners for Mining equipment, Trains, Ships, Green energy, Governments, or military projects. wind turbines,

Contact Information for Business Card

I attached the name and contact info that's on a card, plus the Company Logo. Would like industrial looking background with Bright Colors that will stand out!! If we can insert somewhere maybe on back that we "Custom Manufacture Any Size or Quantity Fastners for Large Mining Equipment, Trains, Ships, Green Energy Equipment or Government Projects

Font styles to use
Other font styles liked:
• You Pick, has to be bold, colorful standout, Professional looking Beable to read it.

Colors

Designer to choose colors to be used in the design.

Requirements
Must have
• Need in Spanish and English TO STANDOUT FROM THE REST OF THE EXPO!! See Business card details, Rounded corners
Nice to have
• Can i see some of the darker cards with Bright Red and Blue letters I like to see the different type of card material, heavy thickness, plastic, transparent, Metal types, Bright Colors, I saw like Raised letters like on the logo.

```html
<!DOCTYPE html>
<html lang="en">
<head>
<meta charset="UTF-8">
<title>KRV Business Cards</title>
<link href="https://fonts.googleapis.com/css2?family=Poppins:wght@400;500;600&display=swap" rel="stylesheet">
<style>
  :root{
    --stage:#1c1c1d;
    --card-white:#ffffff;
    --ink:#2c2c2e;
    --logo-grey:#3d3e42;
    --steel-top:#6a6b6f;
    --steel-bottom:#1f2022;
    --wave-grey:#4a4b4f;
    --wave-blue:#0f3aa6;
    --bright-red:#ff2a2a;
    --bright-blue:#4da3ff;
    --text-light:#ffffff;
  }
  *{margin:0;padding:0;box-sizing:border-box}
  html,body{width:1200px;height:1015px;overflow:hidden;background:var(--stage)}
  body{font-family:"Poppins",sans-serif;position:relative}
  .card{
    position:absolute;left:220px;width:760px;height:434px;
    background:var(--card-white);border-radius:14px;overflow:hidden;
    box-shadow:0 14px 30px rgba(0,0,0,.55);
  }
  .card--front{top:50px}
  .card--back{top:531px}
  .brand-name{
    font-family:"Poppins",sans-serif;font-weight:500;color:var(--logo-grey);
    letter-spacing:14px;line-height:1;
  }
  .card--front .brand-name{
    position:absolute;top:92px;left:0;right:0;text-align:center;font-size:104px;
  }
  .tagline{
    position:absolute;top:262px;left:60px;right:60px;text-align:center;
    font-size:21px;line-height:1.3;color:var(--ink);font-weight:400;
  }
  .wave{position:absolute;inset:0;width:760px;height:434px}
  .card--back .brand-name{position:absolute;top:110px;left:70px;font-size:92px}
  .contact{
    position:absolute;right:38px;top:232px;text-align:right;color:var(--text-light);
    font-size:18px;line-height:1.55;
  }
  .contact .person{font-size:22px;font-weight:500;margin-bottom:4px}
  .contact .quote-label{color:var(--bright-red);font-weight:600}
  .contact .email{color:var(--bright-blue);font-weight:500}
  .contact .phones{display:flex;justify-content:flex-end;align-items:center;gap:6px}
  .contact svg{width:16px;height:16px;fill:none;stroke:var(--text-light);stroke-width:2}
</style>
</head>
<body>
  <section class="card card--front">
    <div class="brand-name">KRV</div>
    <p class="tagline">Custom Manufacture Any Size or Quantity Fastners for Large Mining Equipment, Trains, Ships, Green Energy Equipment or Government Projects</p>
  </section>

  <section class="card card--back">
    <svg class="wave" viewBox="0 0 760 434" aria-hidden="true">
      <defs>
        <linearGradient id="steel" x1="0" y1="0" x2="0.3" y2="1">
          <stop offset="0" stop-color="var(--steel-top)"/>
          <stop offset="1" stop-color="var(--steel-bottom)"/>
        </linearGradient>
      </defs>
      <path d="M0,330 C220,300 320,290 440,170 C540,70 620,40 760,40 L760,434 L0,434 Z" fill="url(#steel)"/>
      <path d="M0,318 C220,290 320,272 430,160 C530,62 610,30 720,28" fill="none" stroke="var(--wave-blue)" stroke-width="9"/>
      <path d="M0,300 C200,280 310,258 415,150 C470,95 500,75 520,62" fill="none" stroke="var(--wave-grey)" stroke-width="8"/>
    </svg>
    <div class="brand-name">KRV</div>
    <div class="contact">
      <p class="person">Lic.Marisol Ventura Ortega</p>
      <p class="quote-label">Cotizaciones en</p>
      <p class="email">ventas.krvtornillos@correo.mx</p>
      <p class="phones">5550142288
        <svg viewBox="0 0 16 16"><rect x="4" y="1.5" width="8" height="13" rx="1.5"/></svg>
        5550179034
        <svg viewBox="0 0 16 16"><path d="M3 2l3 0 1 3-2 1.5c1 2 2.5 3.5 4.5 4.5L11 9l3 1v3c-6 0.5-11.5-5-11-11z"/></svg>
      </p>
    </div>
  </section>
</body>
</html>
```